Public Relations Agency Seeks Wordpress Design and Coding

TRELVOX Studio is a public relations agency specializing in media relations, public affairs and marketing communication.

The site should display the following visual characteristics: professionalism, trustworthiness, high-tech focus, clear and concise design.

The desired colors are royal blue, gray and hints of red.

Design look/feel inspired by this site: http://brightpathgatherings.example/

Specifications:

1. Navigation/Pages/Index:

HOME

ABOUT US

SERVICES

NEWS

CONTACT

---

2. Functionality of/content for each page:

- Home
o Dominant photo (professional, edgy, innovative)
o Simple, straightforward access to/from “Home” from other pages
o Includes logo (attached) and tagline "Unleash the power of communication"
o Direct link to “CONTACT”
o Links to social media accounts: Facebook, Twitter, LinkedIn

- About Us

o Company profile blurb
o President’s photo with short bio

- Services
o Public Relations
 Strategic communication
 Brand and reputation management
 Community relations
o Media Relations
 News coverage and contacts
 Media training and interview skills
 Crisis communications
o Congressional Affairs
 Public affairs
 Public policy
 Legislative strategy
o Mass Communication
 Speechwriting
 Presentation creation
 Social media
o Marketing Communications
 Business collateral material
 Promotional campaigns
 Special events and tradeshows

- News
o Blog-like page to post information and/or share news from other sites

- Contact
o Standard “Contact Us” form (Name, Email, Phone, Message)
o Direct Contact
 (407) 555-0164
 Marisol@TRELVOXstudio.example

Target Market(s)

Small to large businesses specializing in high technology, defense/military, medicine/healthcare, and wide array of professional services.

Industry/Entity Type

Marketing

Font styles to use
Serif
Sans Serif

Colors
0555a3
ec2027
edf3f7

Requirements
Must have
• -- Project reqires DESIGN - and - fully CODED.

-- Strong SEO

-- Optimized for mobile viewing

Thank you!

```html
<!DOCTYPE html>
<html lang="en">
<head>
<meta charset="utf-8">
<title>TRELVOX Studio – Public Relations Agency</title>
<link rel="stylesheet" href="https://fonts.googleapis.com/css2?family=Hind:wght@500;600;700&family=Open+Sans:wght@400;600;700&family=Lora:wght@400&display=swap">
<style>
:root{
  --red:#d5311f;
  --red-bright:#ec2027;
  --blue:#0555a3;
  --blue-light:#1a78c2;
  --ice:#edf3f7;
  --grey-bg:#ececec;
  --text:#555;
  --dark:#1b1b1b;
  --white:#fff;
  --yellow:#f3c316;
  --green:#5aaa32;
}
*{box-sizing:border-box;margin:0;padding:0}
html,body{width:1200px;height:3087px;overflow:hidden}
body{font-family:"Open Sans",Arial,sans-serif;color:var(--text);background:var(--white);position:relative}
.wrap{width:1002px;margin:0 auto;position:relative;height:100%}
h2{font-family:"Hind",Arial,sans-serif;font-weight:700}

/* header */
.site-header{height:99px;border-top:4px solid var(--red);background:var(--white)}
.logo{position:absolute;left:0;top:30px;display:flex;align-items:center;gap:10px;font-family:"Hind",sans-serif;font-weight:600;font-size:34px;color:#444;letter-spacing:1px}
.logo-mark{width:14px;height:14px;background:var(--red)}
.main-nav{position:absolute;right:0;top:32px;display:flex;align-items:center;gap:0}
.main-nav a{font-size:14px;color:#222;text-decoration:none;padding:10px 18px;border-radius:6px;margin-left:8px}
.main-nav a.active{background:var(--red);color:var(--white);padding:10px 22px}

/* hero */
.hero{height:510px;position:relative;background:radial-gradient(ellipse at 50% 45%,#d9a56f 0%,#a8693a 45%,#5a3518 100%)}
.hero-art{position:absolute;inset:0}
.hero-caption{position:absolute;left:101px;top:203px;width:519px;height:75px;background:rgba(12,12,12,.82);color:var(--white);font-size:24px;line-height:75px;padding-left:42px}
.hero-arrow{position:absolute;top:216px;width:52px;height:55px;background:rgba(20,20,20,.85);display:flex;align-items:center;justify-content:center}
.hero-arrow.prev{left:0}.hero-arrow.next{right:0}
.hero-dots{position:absolute;left:572px;top:466px;display:flex;gap:6px}
.hero-dots span{width:10px;height:10px;border-radius:50%;background:var(--white)}
.hero-dots span.on{background:var(--red-bright)}

/* about */
.about{height:200px;text-align:center}
.about h2{color:var(--red);font-size:31px;padding-top:30px;line-height:40px}
.about p{font-size:12.5px;line-height:25px;margin-top:14px;padding:0 2px}

/* services */
.services{height:424px;background:linear-gradient(160deg,#5d4a3c 0%,#3c3029 45%,#6a5240 100%);color:var(--white);text-align:center}
.services h2{font-size:30px;padding-top:26px;line-height:40px}
.service-list{display:flex;justify-content:space-between;margin-top:52px;padding:0 20px}
.service{width:300px}
.service-icon{width:128px;height:128px;border-radius:50%;border:4px solid var(--white);margin:0 auto;display:flex;align-items:center;justify-content:center}
.service-icon.red{background:#e03a4e}.service-icon.yellow{background:var(--yellow)}.service-icon.blue{background:#0b74c1}
.service h3{font-family:"Open Sans",sans-serif;font-weight:600;font-size:18px;margin-top:22px}
.service p{font-size:12.5px;font-weight:700;line-height:24px;margin-top:10px}
.service .more{font-size:12.5px;display:inline-block;margin-top:4px}
.more.red{color:#e03a4e}.more.yellow{color:var(--yellow)}.more.blue{color:#2b8fd9}

/* technology */
.technology{height:311px;background:var(--grey-bg)}
.tech-photo{position:absolute;left:0;top:41px;width:386px;height:226px;background:linear-gradient(90deg,#6d3234 0%,#8c8a88 30%,#c9a58b 60%,#3a3a3a 100%)}
.tech-body{position:absolute;left:411px;top:44px;right:0}
.tech-body h2{color:var(--red);font-size:31px;line-height:40px}
.tech-body p{font-size:12.5px;line-height:23.4px;margin-top:4px}

/* team */
.team{height:500px;background:linear-gradient(160deg,#4d3e34 0%,#2f2722 50%,#5b4838 100%);text-align:center}
.team h2{color:var(--white);font-size:30px;padding-top:27px;line-height:40px}
.team-list{position:absolute;left:41px;top:176px;display:flex;gap:37px}
.member{width:286px;height:270px;background:var(--white);position:relative;padding-top:94px}
.member-photo{position:absolute;left:61px;top:-86px;width:164px;height:164px;border-radius:50%;background:linear-gradient(160deg,#9a9a9a,#3d3d3d)}
.member:nth-child(2) .member-photo{background:linear-gradient(160deg,#d7b98f,#7a5b3a)}
.member:nth-child(3) .member-photo{background:linear-gradient(160deg,#7f9a7c,#2d3b2b)}
.member h3{font-family:"Lora",Georgia,serif;font-weight:400;font-size:21px;color:#222}
.member .role{font-size:10.5px;color:#2b6fa8;margin-top:6px;letter-spacing:.2px}
.member p{font-size:12px;line-height:21px;margin:8px 36px 0}
.btn-blue{display:inline-block;margin-top:12px;background:var(--blue);color:var(--white);font-size:11.5px;padding:9px 26px;border-radius:4px}

/* news */
.news{height:477px}
.news h2{position:absolute;left:0;top:32px;color:var(--red);font-size:25px;line-height:34px}
.news-card{position:absolute;top:86px;width:333px;height:350px;border:1px solid #ddd;background:var(--white)}
.news-card.one{left:0}.news-card.two{left:360px}
.news-img{height:206px;position:relative}
.news-card.one .news-img{background:linear-gradient(135deg,#2a8c9a,#1c4d62)}
.news-card.two .news-img{background:linear-gradient(135deg,#e8eef3,#b9cddc)}
.news-date{position:absolute;right:0;bottom:0;width:57px;height:62px;background:var(--red);color:var(--white);text-align:center;font-size:12px;padding-top:8px;line-height:22px}
.news-date b{font-size:20px;font-weight:600;display:block}
.news-card h3{font-size:15px;font-weight:700;color:#111;margin:16px 13px 0}
.news-card p{font-size:12px;line-height:19px;margin:8px 13px 0}
.news-card .read{display:block;color:var(--red);font-size:12px;margin:7px 13px 0}
.side{position:absolute;left:708px;top:86px;width:294px}
.quote{height:175px;background:linear-gradient(180deg,#7a7a7a,#6a6a6a 70%,#3b7e9a);text-align:center;color:var(--white);padding-top:40px}
.quote h3{font-family:"Hind",sans-serif;font-weight:500;font-size:24px}
.quote span{display:inline-block;margin-top:12px;background:#1b4d5e;font-size:12px;font-weight:700;padding:7px 34px;border-radius:4px}
.newsletter{height:160px;margin-top:15px;background:linear-gradient(160deg,#1b63b8,#0a4588);color:var(--white);padding:10px 14px}
.newsletter h3{font-family:"Hind",sans-serif;font-weight:500;font-size:20px}
.newsletter p{font-size:11px;font-weight:600;line-height:15px;margin-top:2px;width:260px}
.newsletter .field{margin-top:6px;background:var(--white);height:26px;color:#777;font-size:11px;line-height:26px;padding-left:8px}
.newsletter .send{float:right;margin-top:10px;background:var(--green);font-size:11px;padding:4px 12px}

/* contact */
.contact{height:464px;background:linear-gradient(180deg,#7a8a90 0%,#4d5f67 50%,#2b3a42 100%)}
.contact h2{text-align:center;color:var(--white);font-family:"Hind",sans-serif;font-weight:500;font-size:29px;padding-top:30px;line-height:40px}
.contact-form{position:absolute;left:0;top:99px;width:403px}
.contact-form .input{background:var(--white);height:56px;font-size:13px;color:#999;padding:18px 14px;margin-bottom:16px}
.contact-form .input.msg{height:124px}
.submit{height:45px;background:linear-gradient(180deg,#333,#0f0f0f);color:var(--white);text-align:center;line-height:45px;font-size:14px;border-radius:4px;margin-top:-2px}
.map{position:absolute;left:461px;top:99px;width:541px;height:327px;background:linear-gradient(135deg,#e9e5dc 0%,#d9d3c2 40%,#e6dfa8 70%,#cfd6c4 100%);border:1px solid #bbb}

/* footer */
.site-footer{height:102px;background:var(--dark);color:var(--white)}
.site-footer p{position:absolute;left:0;top:42px;font-size:13px}
.social{position:absolute;right:0;top:34px;display:flex;gap:18px}
.social span{width:32px;height:32px;border-radius:3px}
</style>
</head>
<body>

<header class="site-header">
  <div class="wrap">
    <div class="logo"><span class="logo-mark"></span>TRELVOX Studio</div>
    <nav class="main-nav">
      <a class="active" href="#">Home</a>
      <a href="#">About us</a>
      <a href="#">Services</a>
      <a href="#">News</a>
      <a href="#">Contact us</a>
    </nav>
  </div>
</header>

<section class="hero">
  <div class="hero-art" role="img" aria-label="Photo of laptop, desktop monitor, tablet and phone showing illustrated people using social media"></div>
  <div class="hero-caption">Unleash the power of communication</div>
  <div class="hero-arrow prev"><svg width="16" height="22" viewBox="0 0 16 22"><path d="M12 3 4 11l8 8" fill="none" stroke="#fff" stroke-width="4"/></svg></div>
  <div class="hero-arrow next"><svg width="16" height="22" viewBox="0 0 16 22"><path d="M4 3l8 8-8 8" fill="none" stroke="#fff" stroke-width="4"/></svg></div>
  <div class="hero-dots"><span class="on"></span><span></span><span></span></div>
</section>

<section class="about">
  <div class="wrap">
    <h2>About The Company</h2>
    <p>Lorem ipsum dolor sit amet, consectetuer adipiscing elit, sed diam nonummy nibh euismod tincidunt ut laoreet dolore magna aliquam erat volutpat. Ut wisi enim ad minim veniam, quis nostrud exerci tation ullamcorper suscipit lobortis nisl ut aliquip ex ea commodo consequat. Lorem ipsum dolor sit amet, consectetuer adipiscing elit, sed diam nonummy nibh euismod tincidunt ut laoreet dolore magna aliquam erat volutpat. Ut wisi enim ad minim veniam, quis nostrud exerci tation ullamcorper suscipit lobortis nisl ut aliquip ex ea commodo consequat. Lorem ipsum dolor sit amet, consectetuer adipiscing elit, sed diam</p>
  </div>
</section>

<section class="services" role="img" aria-label="Services section over a photo of a desk with a camera">
  <div class="wrap">
    <h2>Services</h2>
    <div class="service-list">
      <div class="service">
        <div class="service-icon red"><svg width="60" height="60" viewBox="0 0 60 60"><rect x="22" y="6" width="16" height="30" rx="8" fill="#fff"/><path d="M14 28a16 16 0 0 0 32 0" fill="none" stroke="#fff" stroke-width="4"/><path d="M30 44v10M22 54h16" stroke="#fff" stroke-width="4"/></svg></div>
        <h3>Media Relations</h3>
        <p>Lorem ipsum dolor sit amet, consectetuer adip-iscing elit, sed diam nonummy nibh euismod tincidunt ut laoreet at.</p>
        <span class="more red">Read more</span>
      </div>
      <div class="service">
        <div class="service-icon yellow"><svg width="70" height="60" viewBox="0 0 70 60"><circle cx="35" cy="20" r="9" fill="#fff"/><circle cx="16" cy="24" r="7" fill="#fff"/><circle cx="54" cy="24" r="7" fill="#fff"/><path d="M20 50a15 15 0 0 1 30 0z" fill="#fff"/><path d="M4 50a12 12 0 0 1 20-9v9zM66 50a12 12 0 0 0-20-9v9z" fill="#fff"/></svg></div>
        <h3>Public Affairs</h3>
        <p>Lorem ipsum dolor sit amet, consectetuer adip-iscing elit, sed diam nonummy nibh euismod tincidunt ut laoreet at.</p>
        <span class="more yellow">Read more</span>
      </div>
      <div class="service">
        <div class="service-icon blue"><svg width="60" height="60" viewBox="0 0 60 60"><rect x="14" y="6" width="28" height="48" rx="4" fill="none" stroke="#fff" stroke-width="4"/><path d="M20 26h6l12-7v20l-12-7h-6z" fill="#fff"/><path d="M44 22l8-4M44 29h9M44 36l8 4" stroke="#fff" stroke-width="3"/></svg></div>
        <h3>Marketing Communication</h3>
        <p>Lorem ipsum dolor sit amet, consectetuer adip-iscing elit, sed diam nonummy nibh euismod tincidunt ut laoreet at.</p>
        <span class="more blue">Read more</span>
      </div>
    </div>
  </div>
</section>

<section class="technology">
  <div class="wrap">
    <div class="tech-photo" role="img" aria-label="Portrait photo of the agency president"></div>
    <div class="tech-body">
      <h2>Technology</h2>
      <p>Lorem ipsum dolor sit amet, consectetuer adipiscing elit, sed diam nonummy nibh euismod tincidunt ut laoreet dolore magna aliquam erat volutpat. Ut wisi enim ad minim veniam, quis nostrud exerci tation ullamcorper suscipit lobortis nisl ut aliquip ex ea commodo consequat. Lorem ipsum dolor sit amet, consectetuer adipiscing elit, sed diam nonummy nibh euismod tincidunt ut laoreet dolore magna aliquam erat volutpat. Ut wisi enim ad minim veniam, quis nostrud exerci tation ullamcorper suscipit lobortis nisl ut aliquip ex ea commodo consequat. Lorem ipsum dolor sit amet, consectetuer adipiscing elit, sed diam nonummy nibh euismod tincidunt ut laoreet dolore magna aliquam erat volutpat. Ut wisi enim ad minim veniam, quis nostrud exerci tation ullamcorper suscipit</p>
    </div>
  </div>
</section>

<section class="team" role="img" aria-label="Team section over a photo of a desk">
  <div class="wrap">
    <h2>Team</h2>
    <div class="team-list">
      <div class="member">
        <div class="member-photo" role="img" aria-label="Portrait photo of Owen Drace"></div>
        <h3>Owen Drace</h3>
        <div class="role">PARTNER / STRATEGY AND PLANNING</div>
        <p>Egestas dignissim a enim lorem a mus egestas risus porta? Sed. Scelerisque,</p>
        <span class="btn-blue">Read More</span>
      </div>
      <div class="member">
        <div class="member-photo" role="img" aria-label="Portrait photo of Lydia Farrow"></div>
        <h3>Lydia Farrow</h3>
        <div class="role">PARTNER / STRATEGY AND PLANNING</div>
        <p>Egestas dignissim a enim lorem a mus egestas risus porta? Sed. Scelerisque,</p>
        <span class="btn-blue">Read More</span>
      </div>
      <div class="member">
        <div class="member-photo" role="img" aria-label="Portrait photo of Colin Merrit"></div>
        <h3>Colin Merrit</h3>
        <div class="role">PARTNER / STRATEGY AND PLANNING</div>
        <p>Egestas dignissim a enim lorem a mus egestas risus porta? Sed. Scelerisque,</p>
        <span class="btn-blue">Read More</span>
      </div>
    </div>
  </div>
</section>

<section class="news">
  <div class="wrap">
    <h2>Latest News</h2>
    <article class="news-card one">
      <div class="news-img" role="img" aria-label="Illustration of a megaphone surrounded by social media symbols">
        <div class="news-date">Sun<b>12</b></div>
      </div>
      <h3>Lorem ipsum</h3>
      <p>Lorem ipsum dolor sit amet, consectetuer adipiscing elit, sed diam nonummy nibh euismod tincidunt ut laoreet dolore magna aliquam erat volutpat.</p>
      <span class="read">Read More...</span>
    </article>
    <article class="news-card two">
      <div class="news-img" role="img" aria-label="Illustration of a hand touching a network of social media bubbles">
        <div class="news-date">Sun<b>12</b></div>
      </div>
      <h3>Lorem ipsum</h3>
      <p>Lorem ipsum dolor sit amet, consectetuer adipiscing elit, sed diam nonummy nibh euismod tincidunt ut laoreet dolore magna aliquam erat volutpat.</p>
      <span class="read">Read More...</span>
    </article>
    <aside class="side">
      <div class="quote" role="img" aria-label="Free quote banner over a photo of painted fingertips">
        <h3>Free Quote</h3>
        <span>CLICK HERE</span>
      </div>
      <div class="newsletter">
        <h3>NewsLetters</h3>
        <p>Find a office nearest you by entering your zip code below</p>
        <div class="field">Email</div>
        <span class="send">Send</span>
      </div>
    </aside>
  </div>
</section>

<section class="contact" role="img" aria-label="Contact section over a blurred city photo">
  <div class="wrap">
    <h2>Contact Us</h2>
    <div class="contact-form">
      <div class="input">Your Name</div>
      <div class="input">Your Email</div>
      <div class="input msg">Message</div>
      <div class="submit">Submit</div>
    </div>
    <div class="map" role="img" aria-label="Street map showing the office location"></div>
  </div>
</section>

<footer class="site-footer">
  <div class="wrap">
    <p>© 2014 Trelvoxstudio All Rights Reserved</p>
    <div class="social">
      <span style="background:#3b5a9a"></span>
      <span style="background:#2fa9e0"></span>
      <span style="background:#8a8a8a"></span>
      <span style="background:#1a7bb8"></span>
    </div>
  </div>
</footer>

</body>
</html>
```